Briloran Clear Springs needs a new business card design (we produce and sell pure bottled water)

We need a clean modern design for our new business cards, We have an existing logo which ultimately cannot be changed, however it could be slighty improved and the colours adjusted. We have this existing logo on all of our bottles, vehicles etc.

Our company slogan is "Clear with each sip you take".
Along with our relevant company information
(Address, phone, website email etc) we will only be using names and not putting position titles for flexibilty.

We are looking for a clean, minimalist modern design.

You can view our website (if need of an update also!) to see our business.

Industry/Entity Type

Business

Contact Information for Business Card

Staff Name : XXXXXX XXXXXX
Address : 9/41 Tavenor St
Halden Rise QLD 4172
Staff Mobile Number : 04XX XXX XXX
Office Phone Number : 07 3918 2457
Staff Email Address : XXXX@brilorancleargo.com.au
Website : www.brilorancleargo.com.au

Font styles to use
Sans Serif

Colors
cee9f5
33a6d7
0492cd
0455a3
3276b5
85abd2
cedeed

Requirements
Must have
• The ability to edit and change the staff members details as we will need to edit for each respective staff member (7 in total)

```html
<!DOCTYPE html>
<html lang="en">
<head>
<meta charset="utf-8">
<title>Briloran Clear Springs – Business Card</title>
<link href="https://fonts.googleapis.com/css2?family=Archivo+Black&family=Source+Sans+3:wght@400;600;800&display=swap" rel="stylesheet">
<style>
  :root {
    --backdrop-top: #2b2b2b;
    --backdrop-bottom: #050505;
    --card-light: #f3f3f3;
    --brand-deep: #0455a3;
    --brand-bright: #0492cd;
    --ink: #1e1e1e;
    --white: #ffffff;
    --slogan-shadow: #000000;
  }
  * { margin: 0; padding: 0; box-sizing: border-box; }
  html, body { width: 1200px; height: 900px; overflow: hidden; }
  body {
    position: relative;
    background: linear-gradient(to bottom, var(--backdrop-top), var(--backdrop-bottom));
    font-family: "Source Sans 3", "Myriad Pro", sans-serif;
  }
  .card {
    position: absolute;
    top: 184px;
    height: 490px;
    border-radius: 12px;
  }
  .card--front { left: 299px; width: 301px; background: var(--card-light); }
  .card--back  { left: 645px; width: 304px; background: var(--brand-deep); }

  .brand {
    position: absolute;
    left: 0; right: 0; top: 58px;
    display: flex;
    flex-direction: column;
    align-items: center;
  }
  .brand__dot {
    width: 76px; height: 76px;
    border-radius: 50%;
    background: var(--brand-deep);
    margin-bottom: 16px;
  }
  .brand__name {
    color: var(--brand-deep);
    font-weight: 800;
    font-size: 25px;
    line-height: 26px;
    text-align: center;
    text-transform: uppercase;
  }

  .staff {
    position: absolute;
    left: 0; right: 0; top: 276px;
    text-align: center;
    color: var(--ink);
    font-size: 14px;
    line-height: 17.5px;
  }
  .staff__name {
    color: var(--brand-bright);
    font-weight: 600;
    font-size: 17px;
    line-height: 20px;
    margin-bottom: 24px;
  }
  .staff__address { margin-bottom: 13px; }

  .slogan {
    position: absolute;
    left: 0; right: 0; top: 54px;
    text-align: center;
    color: var(--white);
    font-family: "Archivo Black", "Arial Black", sans-serif;
    text-transform: uppercase;
    text-shadow: 4px 4px 0 var(--slogan-shadow);
  }
  .slogan__line { display: block; font-size: 48px; line-height: 60px; }
  .slogan__line--large { font-size: 64px; line-height: 84px; }
</style>
</head>
<body>
  <section class="card card--front">
    <div class="brand">
      <div class="brand__dot"></div>
      <div class="brand__name">Briloran<br>Clear Springs</div>
    </div>
    <div class="staff">
      <p class="staff__name">Marcus Delvane</p>
      <p class="staff__address">9/41 Tavenor St<br>Halden Rise QLD 4172</p>
      <p class="staff__contact">
        0400 618 239<br>
        07 3918 2457<br>
        info@brilorancleargo.com.au<br>
        www.brilorancleargo.com.au
      </p>
    </div>
  </section>

  <section class="card card--back">
    <h1 class="slogan">
      <span class="slogan__line">Clear</span>
      <span class="slogan__line">With</span>
      <span class="slogan__line">Each</span>
      <span class="slogan__line slogan__line--large">Sip</span>
      <span class="slogan__line">You</span>
      <span class="slogan__line">Take</span>
    </h1>
  </section>
</body>
</html>
```